Need Web Design for Business Process Outsourcing Company (Quorvane)

Quorvane is a business process outsourcing company. Need a simple site similar to http://www.tallowbrinkhire.com/ but with a more professional and credible look. New to the process; not sure where to start and comparing my options. Please let me know what my options are if I choose to go with you. Logo is attached for your reference. Please use same colorway

Reason: I want the final product to be coded. Please confirm you will be able to code final design.

Industry/Entity Type

Business

Coding

Coded - Design and coding required

```html
<!DOCTYPE html>
<html lang="en">
<head>
<meta charset="utf-8">
<title>Quorvane Services</title>
<link href="https://fonts.googleapis.com/css2?family=Open+Sans:wght@400;600;700&family=Roboto+Condensed:wght@400;700&display=swap" rel="stylesheet">
<style>
:root{
  --blue:#1b8fd8;
  --blue-dark:#1479b9;
  --navy:#123f63;
  --ink:#2b2b2b;
  --muted:#6d6d6d;
  --light:#eeeeee;
  --footer:#222222;
  --footer-deep:#161616;
  --white:#ffffff;
}
*{box-sizing:border-box;margin:0;padding:0}
html,body{width:1200px;height:3672px;overflow:hidden}
body{font-family:"Open Sans",sans-serif;color:var(--ink);background:var(--white);font-size:15px;line-height:1.55}
.heading{font-family:"Roboto Condensed",sans-serif;font-weight:700;text-transform:uppercase}
.btn{display:inline-block;font-family:"Roboto Condensed",sans-serif;font-weight:700;font-size:15px;text-transform:uppercase;padding:11px 22px;border-radius:3px;letter-spacing:.5px}
.btn-navy{background:var(--navy);color:var(--white)}
.btn-blue{background:var(--blue);color:var(--white)}
.btn-white{background:var(--white);color:var(--navy)}

/* header */
.site-header{height:120px;display:flex;justify-content:space-between;align-items:center;padding:0 60px}
.brand{display:flex;align-items:center;gap:14px}
.brand-mark{width:52px;height:52px;background:var(--blue)}
.brand-name{font-family:"Roboto Condensed",sans-serif;font-weight:700;font-size:40px;line-height:1;color:var(--navy)}
.brand-tag{display:block;font-family:"Roboto Condensed",sans-serif;font-weight:700;font-size:15px;letter-spacing:8px;color:var(--navy);margin-top:4px}
.call{display:flex;align-items:center;gap:14px}
.call-label{font-size:15px;color:var(--muted)}
.call-number{font-family:"Roboto Condensed",sans-serif;font-weight:700;font-size:30px;color:var(--blue);line-height:1}

/* nav */
.main-nav{height:56px;background:var(--blue);display:flex;padding:0 60px}
.main-nav a{color:var(--white);font-family:"Roboto Condensed",sans-serif;font-size:15px;text-transform:uppercase;padding:0 26px;display:flex;align-items:center}
.main-nav a.active{background:var(--navy)}

/* hero */
.hero{position:relative;height:564px;background:linear-gradient(100deg,#cfd3d6 0%,#9ea6ad 38%,#3b4752 70%,#1f2a34 100%)}
.hero-photo{position:absolute;inset:0}
.hero-title{position:absolute;left:60px;top:140px;background:rgba(25,30,36,.75);padding:10px 22px;color:var(--white);font-size:50px;letter-spacing:1px}
.hero-sub{position:absolute;left:60px;top:224px;background:rgba(25,30,36,.75);padding:6px 22px;color:var(--white);font-size:24px}
.hero .btn{position:absolute;left:60px;top:300px}

/* contact form */
.contact-card{position:absolute;left:120px;top:640px;width:220px;height:420px;background:var(--navy);padding:0 0 18px;z-index:2}
.contact-card h3{background:var(--blue);color:var(--white);font-size:17px;padding:12px 20px;margin-bottom:16px}
.field{margin:0 20px 12px;height:38px;background:var(--white);border:1px solid #cfd6dc;color:#9aa3aa;font-size:13px;padding:9px 10px}
.field.tall{height:64px}
.contact-card .btn{margin-left:20px;background:#2b2b2b;font-size:13px;padding:8px 16px}

/* welcome */
.welcome{height:360px;background:var(--light);padding:60px 120px 0 420px}
.welcome h2{font-size:42px;color:var(--ink);font-weight:400;font-family:"Roboto Condensed",sans-serif;margin-bottom:20px}
.welcome p{font-size:14px;color:var(--muted);margin-bottom:24px}

.section-title{font-size:46px;text-align:center;color:var(--ink);font-weight:400}
.section-title b{color:var(--blue);font-weight:400}
.section-lede{font-size:14px;color:var(--muted);text-align:center;width:640px;margin:20px auto 0}

/* experience */
.experience{height:600px;padding-top:60px}
.card-row{display:flex;gap:32px;padding:0 80px;margin-top:56px}
.card{width:232px}
.card-img{height:158px;background:linear-gradient(135deg,#dfe6ec,#9fb3c4)}
.card h4{font-family:"Roboto Condensed",sans-serif;color:var(--blue);font-size:21px;margin:14px 0 4px;font-weight:700}
.card p{font-size:13px;color:var(--muted)}
.card .more{color:var(--blue);font-weight:700;font-size:12px;text-transform:uppercase;margin-left:10px}

/* services */
.services{height:480px;background:var(--blue);color:var(--white);padding-top:56px;text-align:center}
.services .section-title,.services .section-lede{color:var(--white)}
.service-row{display:flex;justify-content:center;gap:40px;margin-top:40px}
.service{width:200px}
.service svg{margin:0 auto 12px;display:block}
.service h4{font-family:"Roboto Condensed",sans-serif;font-size:21px;margin-bottom:6px}
.service p{font-size:13px}
.services .btn{margin-top:24px;font-size:13px;padding:8px 20px}

/* strategy */
.strategy{height:480px;background:var(--light);padding-top:56px;text-align:center}
.strategy-row{display:flex;justify-content:center;gap:40px;margin-top:48px;text-align:left}
.strategy-item{display:flex;gap:18px;width:280px}
.strategy-icon{width:90px;height:90px;flex:none;background:var(--navy);display:flex;align-items:center;justify-content:center}
.strategy-item h4{font-family:"Roboto Condensed",sans-serif;color:var(--blue);font-size:21px;font-weight:400}
.strategy-item p{font-size:13px;color:var(--muted)}
.strategy .btn{margin-top:40px;font-size:13px;padding:9px 20px}

/* news */
.news{height:540px;padding-top:60px}
.news .card-row{margin-top:40px}
.news .card-img{height:148px;background:linear-gradient(135deg,#e8ecef,#a9b6c1)}
.news h5{font-size:13px;color:var(--blue);font-weight:600;margin-top:12px}
.news .date{font-size:12px;color:var(--muted);display:flex;align-items:center;gap:6px;margin:4px 0}

/* security */
.security{height:120px;background:var(--blue);display:flex;align-items:center;padding:0 80px 0 160px;color:var(--white);gap:24px}
.security h3{font-size:36px;font-weight:400;font-family:"Roboto Condensed",sans-serif;line-height:1}
.security p{font-size:14px}
.security .btn{margin-left:auto;font-size:14px;padding:10px 22px}

/* footer */
.site-footer{height:320px;background:var(--footer);color:#bdbdbd;display:flex;padding:50px 80px 0;gap:60px;font-size:13px}
.site-footer h4{color:var(--white);font-size:16px;font-weight:600;margin-bottom:12px}
.footer-brand{width:240px}
.footer-brand .brand-name{color:var(--white)}
.footer-brand .brand-tag{color:var(--white)}
.footer-brand p{margin-top:18px}
.footer-col{width:200px}
.footer-col ul{list-style:none;line-height:1.75}
.testimonial{width:240px}
.client{color:var(--blue);font-weight:600;text-transform:uppercase;margin-top:4px}
.arrows{display:flex;gap:8px;margin-top:18px}
.arrows span{width:28px;height:28px;background:#3a3a3a;display:flex;align-items:center;justify-content:center}
.touch li{display:flex;gap:10px;align-items:flex-start;margin-bottom:10px}
.socials{display:flex;gap:12px;margin-top:10px}
.socials span{width:38px;height:38px;border-radius:50%;background:var(--blue)}
.copyright{height:32px;background:var(--footer-deep);color:#9a9a9a;font-size:12px;display:flex;align-items:center;justify-content:center}
</style>
</head>
<body>

<header class="site-header">
  <div class="brand">
    <span class="brand-mark"></span>
    <div><span class="brand-name">Quorvane</span><span class="brand-tag">SERVICES</span></div>
  </div>
  <div class="call">
    <svg width="34" height="34" viewBox="0 0 24 24"><path fill="#1b8fd8" d="M6.6 10.8a15.1 15.1 0 0 0 6.6 6.6l2.2-2.2c.3-.3.7-.4 1-.2 1.1.4 2.3.6 3.6.6.6 0 1 .4 1 1V20c0 .6-.4 1-1 1A17 17 0 0 1 3 4c0-.6.4-1 1-1h3.5c.6 0 1 .4 1 1 0 1.3.2 2.5.6 3.6.1.3 0 .7-.2 1z"/></svg>
    <div><div class="call-label">Call Us Now</div><div class="call-number">(123) 456-7890</div></div>
  </div>
</header>

<nav class="main-nav">
  <a class="active">Home</a><a>Who We Are</a><a>Services</a><a>Strategy</a><a>Experience</a><a>Security</a><a>News</a><a>Contact Us</a>
</nav>

<section class="hero">
  <div class="hero-photo" role="img" aria-label="Businessman in a suit holding a tablet with a glowing globe and floating app icons"></div>
  <h1 class="hero-title heading">Quorvane Services</h1>
  <p class="hero-sub">Lorem Ipsum is simply dummy</p>
  <a class="btn btn-blue">Contact Us Now</a>
</section>

<form class="contact-card">
  <h3 class="heading">Contact Us</h3>
  <div class="field">Name</div>
  <div class="field">Email</div>
  <div class="field">Company</div>
  <div class="field">Phone no</div>
  <div class="field tall">Message</div>
  <a class="btn">Submit</a>
</form>

<section class="welcome">
  <h2 class="heading">Welcome to <span style="color:var(--blue)">Quorvane Services</span></h2>
  <p>Lorem Ipsum is simply dummy text of the printing and typesetting industry. Lorem Ipsum has been the industry's standard dummy text ever since the 1500s, when an unknown printer took a galley of type and scrambled it to make a type specimen book. It has survived not only five centuries, but also the leap into electronic typesetting, remaining essentially unchanged. It was popularised in the 1960s with the release of Letraset sheets containing Lorem Ipsum passages.</p>
  <a class="btn btn-navy">Read More &#187;</a>
</section>

<section class="experience">
  <h2 class="section-title heading">Our <b>Experience</b></h2>
  <p class="section-lede">Lorem Ipsum is simply dummy text of the printing and typesetting industry. Lorem Ipsum has been the industry's standard dummy text ever since the 1500s.</p>
  <div class="card-row">
    <article class="card"><div class="card-img" role="img" aria-label="Team meeting around a laptop"></div><h4>Lorem Ipsum is simply</h4><p>dummy text of the... <span class="more">Read More &#187;</span></p></article>
    <article class="card"><div class="card-img" role="img" aria-label="Hand drawing a rising business chart"></div><h4>Lorem Ipsum is simply</h4><p>dummy text of the... <span class="more">Read More &#187;</span></p></article>
    <article class="card"><div class="card-img" role="img" aria-label="Colleagues working in a bright office"></div><h4>Lorem Ipsum is simply</h4><p>dummy text of the... <span class="more">Read More &#187;</span></p></article>
    <article class="card"><div class="card-img" role="img" aria-label="Business people discussing documents at a desk"></div><h4>Lorem Ipsum is simply</h4><p>dummy text of the... <span class="more">Read More &#187;</span></p></article>
  </div>
</section>

<section class="services">
  <h2 class="section-title heading">Outsourcing Services</h2>
  <p class="section-lede">Lorem Ipsum is simply dummy text of the printing and typesetting industry. Lorem Ipsum has been the industry's standard.</p>
  <div class="service-row">
    <div class="service">
      <svg width="48" height="48" viewBox="0 0 24 24" fill="#fff"><path d="M1 3h3l2.6 11h11.8L21 6H6.2L5.6 3.8"/><circle cx="8" cy="19" r="2"/><circle cx="17" cy="19" r="2"/></svg>
      <h4>Customer Service</h4><p>Lorem Ipsum is simply dummy text of the printing and typesetting industry.</p>
    </div>
    <div class="service">
      <svg width="48" height="48" viewBox="0 0 24 24" fill="#fff"><path d="M3 9h18l-2 11H5z"/><path d="M8 9V6a4 4 0 0 1 8 0v3" fill="none" stroke="#fff" stroke-width="2"/></svg>
      <h4>Ecommerce</h4><p>Lorem Ipsum is simply dummy text of the printing and typesetting industry.</p>
    </div>
    <div class="service">
      <svg width="48" height="48" viewBox="0 0 24 24" fill="#fff"><circle cx="12" cy="10" r="6"/><rect x="9" y="16" width="6" height="5"/></svg>
      <h4>Creative</h4><p>Lorem Ipsum is simply dummy text of the printing and typesetting industry.</p>
    </div>
    <div class="service">
      <svg width="48" height="48" viewBox="0 0 24 24" fill="none" stroke="#fff" stroke-width="2.4"><circle cx="12" cy="12" r="4"/><path d="M12 2v4M12 18v4M2 12h4M18 12h4M5 5l3 3M16 16l3 3M5 19l3-3M16 8l3-3"/></svg>
      <h4>IT Solutions</h4><p>Lorem Ipsum is simply dummy text of the printing and typesetting industry.</p>
    </div>
  </div>
  <a class="btn btn-white">View All &#187;</a>
</section>

<section class="strategy">
  <h2 class="section-title heading">Our <b>Strategy</b></h2>
  <p class="section-lede">Lorem Ipsum is simply dummy text of the printing and typesetting industry. Lorem Ipsum has been the industry's standard dummy text ever since the 1500s.</p>
  <div class="strategy-row">
    <div class="strategy-item">
      <div class="strategy-icon"><svg width="46" height="46" viewBox="0 0 24 24" fill="#fff"><circle cx="8" cy="8" r="3"/><circle cx="16" cy="8" r="3"/><path d="M2 19a6 6 0 0 1 12 0zM10 19a6 6 0 0 1 12 0z"/></svg></div>
      <div><h4>Lorem Ipsum</h4><p>Lorem Ipsum is simply dummy text of the printing and typesetting...</p></div>
    </div>
    <div class="strategy-item">
      <div class="strategy-icon"><svg width="46" height="46" viewBox="0 0 24 24" fill="none" stroke="#fff" stroke-width="2"><rect x="3" y="4" width="18" height="12"/><path d="M6 13l4-4 3 3 5-5M12 16v4M8 20h8"/></svg></div>
      <div><h4>Lorem Ipsum</h4><p>Lorem Ipsum is simply dummy text of the printing and typesetting...</p></div>
    </div>
    <div class="strategy-item">
      <div class="strategy-icon"><svg width="46" height="46" viewBox="0 0 24 24" fill="#fff"><circle cx="12" cy="9" r="4"/><path d="M4 21a8 8 0 0 1 16 0z"/></svg></div>
      <div><h4>Lorem Ipsum</h4><p>Lorem Ipsum is simply dummy text of the printing and typesetting...</p></div>
    </div>
  </div>
  <a class="btn btn-navy">Know More &#187;</a>
</section>

<section class="news">
  <h2 class="section-title heading">Latest <b>News</b></h2>
  <div class="card-row">
    <article class="card"><div class="card-img" role="img" aria-label="Business people shaking hands"></div><h5>Lorem Ipsum is simply dummy text of the printing</h5><div class="date"><svg width="12" height="12" viewBox="0 0 24 24" fill="#1b8fd8"><rect x="3" y="5" width="18" height="16"/></svg>November 16, 2016</div><p>Lorem Ipsum is simply dummy text of the printing and typesetting industry.</p></article>
    <article class="card"><div class="card-img" role="img" aria-label="Desk with charts, notebook and calculator"></div><h5>Lorem Ipsum is simply dummy text of the printing</h5><div class="date"><svg width="12" height="12" viewBox="0 0 24 24" fill="#1b8fd8"><rect x="3" y="5" width="18" height="16"/></svg>November 16, 2016</div><p>Lorem Ipsum is simply dummy text of the printing and typesetting industry.</p></article>
    <article class="card"><div class="card-img" role="img" aria-label="Team talking in a meeting room"></div><h5>Lorem Ipsum is simply dummy text of the printing</h5><div class="date"><svg width="12" height="12" viewBox="0 0 24 24" fill="#1b8fd8"><rect x="3" y="5" width="18" height="16"/></svg>November 16, 2016</div><p>Lorem Ipsum is simply dummy text of the printing and typesetting industry.</p></article>
    <article class="card"><div class="card-img" role="img" aria-label="Hand pointing at financial graphs"></div><h5>Lorem Ipsum is simply dummy text of the printing</h5><div class="date"><svg width="12" height="12" viewBox="0 0 24 24" fill="#1b8fd8"><rect x="3" y="5" width="18" height="16"/></svg>November 16, 2016</div><p>Lorem Ipsum is simply dummy text of the printing and typesetting industry.</p></article>
  </div>
</section>

<section class="security">
  <svg width="74" height="80" viewBox="0 0 24 26" fill="none" stroke="#fff" stroke-width="2"><path d="M6 11V7a6 6 0 0 1 12 0v4"/><rect x="3" y="11" width="18" height="13" fill="#fff"/></svg>
  <div><h3 class="heading">Security</h3><p>Lorem Ipsum is simply dummy text of the printing and typesetting industry.</p></div>
  <a class="btn btn-white">Contact Us</a>
</section>

<footer class="site-footer">
  <div class="footer-brand">
    <div class="brand"><span class="brand-mark"></span><div><span class="brand-name">Quorvane</span><span class="brand-tag">SERVICES</span></div></div>
    <p>Lorem Ipsum is simply dummy text of the printing and types.</p>
  </div>
  <div class="footer-col">
    <h4>Useful Links</h4>
    <ul><li>Home</li><li>Who We Are</li><li>Services</li><li>Strategy</li><li>Experience</li><li>Security</li><li>News</li><li>Contact Us</li></ul>
  </div>
  <div class="testimonial">
    <h4>Client Testimonial</h4>
    <p>Lorem Ipsum is simply dummy text of the printing and typesetting industry. Lorem Ipsum has been...</p>
    <p class="client">&mdash; Client Name</p>
    <div class="arrows"><span><svg width="10" height="10" viewBox="0 0 10 10"><path d="M7 1L3 5l4 4" fill="none" stroke="#fff" stroke-width="2"/></svg></span><span><svg width="10" height="10" viewBox="0 0 10 10"><path d="M3 1l4 4-4 4" fill="none" stroke="#fff" stroke-width="2"/></svg></span></div>
  </div>
  <div class="footer-col touch">
    <h4>Get In Touch With Us</h4>
    <ul>
      <li><svg width="14" height="14" viewBox="0 0 24 24" fill="#1b8fd8"><path d="M12 2a7 7 0 0 0-7 7c0 5 7 13 7 13s7-8 7-13a7 7 0 0 0-7-7z"/></svg>Lorem Ipsum is simply dummy text of the printing.</li>
      <li><svg width="14" height="14" viewBox="0 0 24 24" fill="#1b8fd8"><path d="M6.6 10.8a15 15 0 0 0 6.6 6.6l2.2-2.2c.3-.3.7-.4 1-.2 1.1.4 2.3.6 3.6.6.6 0 1 .4 1 1V20c0 .6-.4 1-1 1A17 17 0 0 1 3 4c0-.6.4-1 1-1h3.5c.6 0 1 .4 1 1 0 1.3.2 2.5.6 3.6z"/></svg>123 456 7890</li>
      <li><svg width="14" height="14" viewBox="0 0 24 24" fill="#1b8fd8"><rect x="2" y="5" width="20" height="14"/></svg>Lorem Ipsum</li>
    </ul>
    <div class="socials"><span></span><span></span><span></span></div>
  </div>
</footer>
<div class="copyright">&copy; QUORVANE SERVICES 2016. All Rights Reserved.</div>

</body>
</html>
```